Plate of the Raven: Half-Page Magazine Ad

advertisement in a travel magazine for a casual/fine dining restaurant in the heart of Whitehorse, Yukon
Needs to say that it is located in the Stonefield Hotel, 247 Larch Avenue.

Northern inspired cuisine
plateoftheraven.example

Don't need to use all the pictures

Dimensions: ad is a half-page, dimensions are 7.25" x 4.8".

Target Market(s)

Upscale dining, corporate travellers

Industry/Entity Type

Restaurant

Colors
0054AA
0677BA
7BADD7
CADEEF
E8F1F8
0094D4
00A9DD
6FCCEA
C7EBF8
E9F6FB
00AB8E
00BBA5
67D7C9
C6EFE9
E9F9F6

Requirements
Must have
• Restaurant logo
Nice to have
• Simple, clean design with upscale feel

```html
<!DOCTYPE html>
<html lang="en">
<head>
<meta charset="utf-8">
<title>Plate of the Raven – Half-Page Ad</title>
<link rel="stylesheet" href="https://fonts.googleapis.com/css2?family=Lato:wght@400;700;900&display=swap">
<style>
  :root {
    --page-bg: #efefef;
    --card-bg: #ffffff;
    --ink: #1a1a1a;
    --navy: #1f3f7a;
    --forest: #2f7d3a;
    --logo-disc: #cfcfcf;
  }
  html, body {
    margin: 0;
    width: 955px;
    height: 1200px;
    overflow: hidden;
    background: var(--page-bg);
    font-family: "Lato", Arial, sans-serif;
  }
  .ad-sheet {
    width: 955px;
    height: 1200px;
    display: flex;
    flex-direction: column;
    align-items: center;
    justify-content: center;
    gap: 40px;
  }
  .ad-card {
    width: 830px;
    height: 550px;
    background: var(--card-bg);
    box-shadow: 0 2px 6px rgba(0,0,0,0.15);
    display: block;
  }
  .ad-card--navy { --accent: var(--navy); }
  .ad-card--forest { --accent: var(--forest); }
  .accent-fill { fill: var(--accent); }
  .accent-text { fill: var(--accent); }
  .brand-name { font: 900 28px "Lato", Arial, sans-serif; fill: var(--ink); }
  .location-lead { font: 700 18px "Lato", Arial, sans-serif; }
  .location-line { font: 400 20px "Lato", Arial, sans-serif; fill: var(--ink); }
  .band-text { font: 400 27px "Lato", Arial, sans-serif; fill: #ffffff; }
  .phone { font: 900 44px "Lato", Arial, sans-serif; fill: var(--ink); }
  .web { font: 900 30px "Lato", Arial, sans-serif; fill: var(--ink); }
  .photo-frame { stroke: #ffffff; stroke-width: 6; }
</style>
</head>
<body>
<main class="ad-sheet">

  <svg class="ad-card ad-card--navy" viewBox="0 0 830 550" xmlns="http://www.w3.org/2000/svg">
    <defs>
      <clipPath id="card-clip-navy"><rect width="830" height="550"/></clipPath>
      <radialGradient id="dish-navy" cx="0.5" cy="0.4" r="0.6">
        <stop offset="0" stop-color="#8fa44a"/>
        <stop offset="0.35" stop-color="#d9752f"/>
        <stop offset="0.75" stop-color="#c8602a"/>
        <stop offset="1" stop-color="#7a4a2c"/>
      </radialGradient>
      <linearGradient id="interior-navy" x1="0" y1="0" x2="1" y2="1">
        <stop offset="0" stop-color="#d8d8d6"/>
        <stop offset="1" stop-color="#4a4a4a"/>
      </linearGradient>
      <linearGradient id="patio-navy" x1="0" y1="0" x2="1" y2="1">
        <stop offset="0" stop-color="#9ea6a8"/>
        <stop offset="0.6" stop-color="#3d4446"/>
        <stop offset="1" stop-color="#7c5fb0"/>
      </linearGradient>
    </defs>

    <rect class="accent-fill" x="0" y="225" width="460" height="132"/>
    <text class="band-text" text-anchor="middle" x="205" y="262">Open evenings</text>
    <text class="band-text" text-anchor="middle" x="205" y="292">with a</text>
    <text class="band-text" text-anchor="middle" x="205" y="322">Northern inspired</text>
    <text class="band-text" text-anchor="middle" x="205" y="350">cuisine</text>

    <g clip-path="url(#card-clip-navy)">
      <circle class="accent-fill" cx="1000" cy="420" r="560"/>
      <circle cx="1000" cy="420" r="536" fill="url(#dish-navy)" role="img" aria-label="Photo of a plated pasta dish with microgreens and shaved cheese"/>
    </g>

    <circle cx="66" cy="85" r="40" fill="var(--logo-disc)"/>
    <text class="brand-name" x="118" y="78">Plate of</text>
    <text class="brand-name" x="118" y="110">the Raven</text>

    <text class="location-lead accent-text" x="292" y="42">located in the</text>
    <text class="location-line" x="292" y="69">Stonefield Hotel,</text>
    <text class="location-line" x="292" y="95">247 Larch Avenue.</text>

    <circle class="photo-frame" cx="520" cy="222" r="98" fill="url(#interior-navy)" role="img" aria-label="Photo of the restaurant dining room"/>
    <circle class="photo-frame" cx="590" cy="402" r="108" fill="url(#patio-navy)" role="img" aria-label="Photo of the hotel patio with flower baskets"/>

    <text class="phone" x="28" y="448">867-555-0142</text>
    <text class="web" x="28" y="500">plateoftheraven.example</text>
  </svg>

  <svg class="ad-card ad-card--forest" viewBox="0 0 830 550" xmlns="http://www.w3.org/2000/svg">
    <defs>
      <clipPath id="card-clip-forest"><rect width="830" height="550"/></clipPath>
      <radialGradient id="dish-forest" cx="0.5" cy="0.4" r="0.6">
        <stop offset="0" stop-color="#8fa44a"/>
        <stop offset="0.35" stop-color="#d9752f"/>
        <stop offset="0.75" stop-color="#c8602a"/>
        <stop offset="1" stop-color="#7a4a2c"/>
      </radialGradient>
      <linearGradient id="interior-forest" x1="0" y1="0" x2="1" y2="1">
        <stop offset="0" stop-color="#d8d8d6"/>
        <stop offset="1" stop-color="#4a4a4a"/>
      </linearGradient>
      <linearGradient id="patio-forest" x1="0" y1="0" x2="1" y2="1">
        <stop offset="0" stop-color="#9ea6a8"/>
        <stop offset="0.6" stop-color="#3d4446"/>
        <stop offset="1" stop-color="#7c5fb0"/>
      </linearGradient>
    </defs>

    <rect class="accent-fill" x="0" y="225" width="460" height="132"/>
    <text class="band-text" text-anchor="middle" x="205" y="262">Open evenings</text>
    <text class="band-text" text-anchor="middle" x="205" y="292">with a</text>
    <text class="band-text" text-anchor="middle" x="205" y="322">Northern inspired</text>
    <text class="band-text" text-anchor="middle" x="205" y="350">cuisine</text>

    <g clip-path="url(#card-clip-forest)">
      <circle class="accent-fill" cx="1000" cy="420" r="560"/>
      <circle cx="1000" cy="420" r="536" fill="url(#dish-forest)" role="img" aria-label="Photo of a plated pasta dish with microgreens and shaved cheese"/>
    </g>

    <circle cx="66" cy="85" r="40" fill="var(--logo-disc)"/>
    <text class="brand-name" x="118" y="78">Plate of</text>
    <text class="brand-name" x="118" y="110">the Raven</text>

    <text class="location-lead accent-text" x="292" y="42">located in the</text>
    <text class="location-line" x="292" y="69">Stonefield Hotel,</text>
    <text class="location-line" x="292" y="95">247 Larch Avenue.</text>

    <circle class="photo-frame" cx="520" cy="222" r="98" fill="url(#interior-forest)" role="img" aria-label="Photo of the restaurant dining room"/>
    <circle class="photo-frame" cx="590" cy="402" r="108" fill="url(#patio-forest)" role="img" aria-label="Photo of the hotel patio with flower baskets"/>

    <text class="phone" x="28" y="448">867-555-0142</text>
    <text class="web" x="28" y="500">plateoftheraven.example</text>
  </svg>

</main>
</body>
</html>
```